Hop Along Days campaign: promoting kids play in the UK - Website Redesign

Hop Along Days is a national UK campaign that promotes the value of play for children. The current website is live at http://www.hopalongdays.co.uk. This website has been live for 4 years and now needs to be redesigned. The target audience is parents of young children up to the age of 12.

The current site was designed with a series of old adverts in mind. Here is an example of an old advert: http://vidshare.example/qR7tLm2XwZa

Criticisms of existing site:
The design represented the adverts too closely. The result was a website that mirrors the adverts rather than complements them.
The color scheme is too dark.
Text-heavy pages (e.g. http://www.hopalongdays.co.uk/fun.php) are dull and not FUN!

New site
We have recently had a series of new video adverts produced:
advert 1: http://vidshare.example/hB4nVc8JsPe
advert 2: http://vidshare.example/KgW3rTy9DuM
advert 3: http://vidshare.example/zA5oEi1HbNq

The new site should be cleaner and brighter than the existing site, possibly with a white background using graphics, fonts and advert characters (see attached character graphics files) to add the element of fun and play.

The homepage should include:
1. Hop Along Days logo (attached)
2. Social Media links (visible on all pages of the site) – Chatterbook, Chirpline, ClipVault
3. Link to the HopAlongDays app page of the site (visible on all pages)
4. Image/video placeholder that the user can scroll through, view full-size images and play videos.
5. Text area to hold approximately 100 words describing the purpose of the campaign
6. Site footer to contain the same information as on the existing site along with the Northern Games & Crafts Guild logo (attached)

Site structure:
One change to the site structure… the “Brought to you by” menu item will be removed from the top-level menu.

General:
Some pages on the existing site are quite text-heavy, we would like to break up text on these pages in some way. Graphical division of paragraphs, use of advert characters?

Please note that all attached graphics file are the property of the Northern Games & Crafts Guild and must only be used for the purpose of this project.

```html
<!DOCTYPE html>
<html lang="en">
<head>
<meta charset="utf-8">
<title>Hop Along Days</title>
<link href="https://fonts.googleapis.com/css2?family=Source+Sans+3:wght@400;600;700&display=swap" rel="stylesheet">
<style>
:root{
  --purple:#7a5cb8;
  --purple-dark:#5e3f9e;
  --pink:#e8457a;
  --text:#4a4a4a;
  --muted:#8a8a8a;
  --link:#3a5aa8;
  --page:#f3f3f3;
  --panel:#f7f7f7;
  --gold:#f6cf78;
  --footer:#f8d88a;
  --fb:#3b5aa0;
  --cyan:#1fb5e8;
  --lime:#a8d12a;
  --tweet:#2a9fd6;
}
*{box-sizing:border-box;margin:0;padding:0}
html,body{width:934px;height:1200px;overflow:hidden}
body{position:relative;background:var(--page);font-family:"Source Sans 3",sans-serif;color:var(--text);font-size:10.6px;line-height:1.45}
.abs{position:absolute}
/* header */
.site-header{left:0;top:0;width:934px;height:130px;background:linear-gradient(#fbfbfb,#f1f1f1)}
.brand{left:104px;top:40px;width:130px;font-size:24px;font-weight:700;color:var(--purple);line-height:1.05}
.mascot{left:248px;top:4px;width:88px;height:124px;border-radius:40px 40px 10px 10px;background:linear-gradient(#f3a04a,#f7b733 55%,#2d6fb5)}
.main-nav{left:335px;top:58px;width:497px;height:37px;background:linear-gradient(#fff,#ececec);border:1px solid #dcdcdc;border-radius:5px;display:flex;align-items:center}
.main-nav a{display:block;text-decoration:none;color:var(--purple);font-size:11.5px;font-weight:600;padding:0 13px;border-right:1px solid #dcdcdc;line-height:37px;white-space:nowrap}
.main-nav a:last-child{border-right:0}
.main-nav a.active{background:linear-gradient(#9a7fd0,var(--purple));color:#fff;height:46px;line-height:46px;margin-top:-9px;margin-left:20px;border-radius:4px 4px 0 0;padding:0 10px;border-right:0}
/* hero */
.hero-photo{left:0;top:130px;width:598px;height:328px;background:linear-gradient(#bcd9f0 0%,#dfeaf5 30%,#e9b38a 45%,#d25f8e 58%,#9acd3a 70%,#5f9a2a 100%)}
.slider-dots{left:521px;top:437px;display:flex;gap:6px}
.slider-dots span{width:12px;height:12px;background:var(--purple)}
.slider-dots span.on{background:#fff}
.welcome{left:598px;top:130px;width:336px;height:328px;background:linear-gradient(135deg,#fdf1a8,#fbe59c 55%,#f1f1f1)}
.welcome:before{content:"";position:absolute;left:-11px;top:155px;border:11px solid transparent;border-left:0;border-right-color:#fdf1a8}
.welcome h2{position:absolute;left:26px;top:33px;font-size:15px;font-weight:600;color:#333;white-space:nowrap}
.welcome h2 em{font-style:normal;color:var(--purple);font-weight:700}
.welcome .copy{position:absolute;left:26px;top:66px;width:206px;text-align:justify;font-size:10.2px;line-height:15.3px}
.welcome .copy p{margin-bottom:7px}
.btn{display:inline-block;background:var(--purple);color:#fff;font-size:10.2px;padding:3px 7px;border:1px solid #fff;box-shadow:0 0 0 1px #b9a6dc;text-decoration:none}
.welcome .btn{position:absolute;left:27px;top:284px}
/* section headings */
.section-title{font-size:17px;font-weight:400;color:var(--purple);display:flex;align-items:center;gap:4px;white-space:nowrap}
.section-title span{color:var(--pink)}
.section-title:after{content:"";flex:1;height:1px;background:var(--pink);margin-top:8px}
.idea-title{left:103px;top:502px;width:479px}
.gallery-title{left:601px;top:505px;width:196px;font-size:14px}
.gallery-arrows{left:810px;top:503px}
/* play idea */
.idea-art{left:8px;top:540px;width:112px;height:220px;border-radius:50%;background:radial-gradient(circle,#f39a3a,#e2508a 45%,#4aa8c8 80%,transparent 81%)}
.idea-photo{left:110px;top:537px;width:190px;height:190px;border-radius:50%;border:5px solid var(--gold);background:radial-gradient(circle at 45% 45%,#f2c9a5,#e0a070 45%,#3a7ad0 70%,#f1e4c8)}
.idea-copy{left:323px;top:533px;width:259px;text-align:justify;line-height:15.3px}
.idea-copy .btn{margin-top:5px}
/* gallery */
.gallery{left:601px;top:537px;width:231px;height:198px;background:var(--gold);padding:3px}
.gallery-media{position:relative;width:225px;height:112px;background:linear-gradient(#f4f4f4,#fbe1d6 50%,#d8e5c0)}
.gallery-media svg{position:absolute;left:95px;top:37px}
.video-btn{position:absolute;width:91px;height:23px;color:#fff;font-size:15px;font-weight:700;line-height:23px;padding-left:14px;white-space:nowrap}
.v1{left:14px;top:129px;background:var(--purple)}
.v2{left:125px;top:129px;background:var(--cyan)}
.v3{left:14px;top:164px;background:var(--lime)}
.v4{left:125px;top:161px;background:var(--pink)}
.divider{left:80px;top:752px;width:777px;border-top:1px dashed #c9c9c9}
/* widgets */
.girl{left:2px;top:782px;width:100px;height:228px;border-radius:50px 50px 10px 10px;background:linear-gradient(#8a5a3a 0%,#f0c89a 25%,#5fd08a 45%,#3aa86a 62%,#f0b0a8 80%,#e86a6a 100%)}
.widget{top:767px;background:var(--panel);border:1px solid #e3e3e3}
.activity{left:104px;width:233px;height:271px}
.activity-head{height:31px;background:var(--fb);color:#fff;font-size:11.5px;display:flex;justify-content:space-between;align-items:center;padding:0 10px}
.activity-head b{font-weight:700;font-size:11px}
.entry{position:absolute;display:flex;gap:7px}
.avatar{width:51px;height:51px;flex:none;border:1px solid #ccc;background:linear-gradient(#f0f0f0,#c9b6a2 55%,#2a2a2a)}
.activity .entry{left:8px}
.activity .entry p{width:145px;color:var(--link);font-size:10.6px;line-height:14.4px}
.activity .entry small{display:block;color:var(--muted);font-size:9.5px;margin-top:5px}
.plugin{position:absolute;left:8px;top:251px;width:216px;border-top:1px solid #ccc;padding-top:3px;font-size:7.5px;color:#555;display:flex;align-items:center;gap:4px}
.plugin i{width:9px;height:9px;background:var(--fb)}
.tweets{left:351px;width:232px;height:271px;background:#f4f4f4}
.tweets h3{position:absolute;left:8px;top:8px;font-size:13.5px;font-weight:400;color:#333}
.follow{position:absolute;left:92px;top:5px;width:137px;height:22px;border:1px solid #ccc;border-radius:3px;background:linear-gradient(#fff,#e8e8e8);font-size:10px;display:flex;align-items:center;gap:5px;padding-left:8px;color:#333;white-space:nowrap}
.follow i{width:10px;height:10px;border-radius:50%;background:var(--tweet)}
.tweets .entry{left:7px;width:218px}
.tweets .entry p{position:relative;flex:1;font-size:10.6px;line-height:14.4px;color:#333}
.tweets .entry b{font-weight:600}
.tweets .handle,.tweets .age{color:var(--muted)}
.tweets .age{position:absolute;right:0;top:0}
.tweets .tag{color:var(--tweet)}
.tweet-box{position:absolute;left:7px;top:245px;width:218px;height:22px;border:1px solid #ccc;border-radius:3px;background:#fff;font-size:9.5px;line-height:20px;padding-left:8px;color:#555}
.videos{left:599px;width:231px;height:271px}
.video-item{position:absolute;left:0;width:229px;height:69px;border-bottom:1px dashed #c9c9c9;display:flex;gap:9px;padding:5px}
.thumb{position:relative;width:67px;height:51px;flex:none;border:1px solid #999;background:linear-gradient(135deg,#2a2a2a,#6a4a3a 50%,#b22 100%)}
.thumb svg{position:absolute;left:26px;top:17px}
.thumb span{position:absolute;right:2px;bottom:1px;color:#fff;font-size:9.5px;font-weight:700}
.video-item p{width:142px;font-size:10.6px;line-height:14.4px;color:#333;margin-top:-2px}
.video-item small{display:block;color:var(--muted);font-size:9.3px;margin-top:1px}
/* footer */
.site-footer{left:0;top:1060px;width:934px;height:140px;background:var(--footer)}
.site-footer h4{position:absolute;top:12px;font-size:11px;font-weight:600;color:var(--purple-dark);text-transform:uppercase;white-space:nowrap}
.col{position:absolute;top:0}
.quick-links{left:104px}
.quick-links ul{position:absolute;top:38px;list-style:none;width:110px}
.quick-links li{font-size:10.6px;color:#333;height:17.5px;padding-left:10px;position:relative;white-space:nowrap}
.quick-links li:before{content:"";position:absolute;left:0;top:4px;border:3px solid transparent;border-left:4px solid #555;border-right:0}
.contact{left:227px}
.contact div{position:absolute;left:0;width:170px;font-size:10.6px;color:#333;display:flex;gap:5px;line-height:14.5px}
.contact svg{flex:none;margin-top:2px}
.social{left:413px}
.social div{position:absolute;left:0;display:flex;align-items:center;gap:7px;font-size:10.6px;color:#333;white-space:nowrap}
.social i{width:18px;height:18px;border-radius:50%;background:var(--purple)}
.app{position:absolute;left:538px;top:0;width:140px;text-align:center}
.app .device{position:absolute;left:43px;top:27px;width:54px;height:55px;border-radius:6px;background:linear-gradient(#b8e04a,#6aa82a)}
.app p{position:absolute;top:94px;width:140px;font-size:10px;color:#666;white-space:nowrap}
.app p.cta{top:111px;color:var(--pink);font-size:11px}
.guild{position:absolute;left:680px;top:16px;width:144px;text-align:right}
.guild strong{display:block;font-size:13px;font-weight:700;color:#333;line-height:1.15;text-align:center;margin-left:34px}
.guild p{margin-top:8px;font-size:10px;font-weight:600;color:#222;line-height:14px}
</style>
</head>
<body>

<header class="site-header abs">
  <div class="brand abs">Hop Along<br>Days</div>
  <div class="mascot abs" role="img" aria-label="Cartoon girl mascot with red hair and orange dress, arms outstretched"></div>
  <nav class="main-nav abs">
    <a class="active" href="#">PLAY RIGHT NOW</a>
    <a href="#">GET INVLOVED</a>
    <a href="#">WHY PLAY</a>
    <a href="#">FUN FOREVER</a>
    <a href="#">RESOURCES</a>
  </nav>
</header>

<section class="hero">
  <div class="hero-photo abs" role="img" aria-label="Six smiling children lying on green grass under a blue sky"></div>
  <div class="slider-dots abs"><span class="on"></span><span></span><span></span><span></span></div>
  <div class="welcome abs">
    <h2>Welcome to <em>Hop Along Days</em></h2>
    <div class="copy">
      <p>Lorem ipsum dolor sit amet, cons ectetuer adipiscing elit, sed diam enonummy nibh tincidut ufgkdti errrlaoreetna all dolore magna ali quae m erat volutpat. Ut wisi enii</p>
      <p>Lorem ipsum dolor sit amet, cons ectetuer adipiscing elit, sed diam enonummy nibh tincidut ufgkdti errrlaoreetna all dolore magna ali quae m erat volutpat. Ut wisi enii</p>
      <p>Lorem ipsum dolor sit amet, cons ectetuer adipiscing elit, sed diam enonummy nibh tincidut ufgkdti errrlaoreetna all dolore magna ali quae m erat volutpat. Ut wisi enii</p>
    </div>
    <a class="btn" href="#">Read More +</a>
  </div>
</section>

<section class="play-idea">
  <h2 class="section-title idea-title abs">PLAY IDEA <span>OF A</span> DAY</h2>
  <div class="idea-art abs" role="img" aria-label="Colourful swirling flower and ribbon ornament"></div>
  <div class="idea-photo abs" role="img" aria-label="Girl with paint-covered hands held over her face"></div>
  <div class="idea-copy abs">
    <p>Lorem ipsum dolor sit amet, cons ectetuer adipiscingere elit, sed diam enonummy nibh tincidut ufgkdtierererer errrlaoreetna all dolore magna ali quae m erat volutpater Ut wisi enii mad ali quae m eratminimererrmererotpere. Sed diam enonummy nibhereierii tincidut ufgkdtierere errrlaoreetna allii dolore magna ali quae m eratereieerer rmererrmli quaeali quae m erat m erat vali quae m eratolutpatali dolore ma vquaeUt wisi eni m erat Enonummy nibh tincidut ufgkdtierereercfd errrlaoreetna all dolore magna ali quae m erat volutpaerermpreoereer ali quae merat volutpat. Ut wisi enii mad minim.</p>
    <a class="btn" href="#">Read More +</a>
  </div>
</section>

<section class="video-gallery">
  <h2 class="section-title gallery-title abs">VIDEO <span>GALLERY</span></h2>
  <svg class="gallery-arrows abs" width="22" height="14" viewBox="0 0 22 14"><path d="M8 1 2 7l6 6M14 1l6 6-6 6" fill="none" stroke="#888" stroke-width="1.6"/></svg>
  <div class="gallery abs">
    <div class="gallery-media" role="img" aria-label="Two toddlers sitting on the floor playing with toy cars">
      <svg width="34" height="34" viewBox="0 0 34 34"><circle cx="17" cy="17" r="16" fill="#5cc12a" stroke="#fff" stroke-width="2"/><path d="M13 10l11 7-11 7z" fill="#7a5cb8"/></svg>
    </div>
    <a class="video-btn v1">VIDEO 1</a>
    <a class="video-btn v2">VIDEO 2</a>
    <a class="video-btn v3">VIDEO 3</a>
    <a class="video-btn v4">VIDEO 4</a>
  </div>
</section>

<div class="divider abs"></div>

<div class="girl abs" role="img" aria-label="Cartoon girl character in a green dress and striped tights"></div>

<aside class="widget activity abs">
  <div class="activity-head">Recent Activity <b>Chatterbook</b></div>
  <div class="entry" style="top:38px"><div class="avatar" role="img" aria-label="Profile photo"></div><p>Lorem fdaafipsum dafsdolor sit amet, coctetuer adipiscing elit, sed diam<small>2 people recommended this.</small></p></div>
  <div class="entry" style="top:110px"><div class="avatar" role="img" aria-label="Profile photo"></div><p>Lorem fdaafipsum dafsdolor sit amet, coctetuer adipiscing elit, sed diam<small>2 people recommended this.</small></p></div>
  <div class="entry" style="top:183px"><div class="avatar" role="img" aria-label="Profile photo"></div><p>Lorem fdaafipsum dafsdolor sit amet, coctetuer adipiscing elit, sed diam<small>2 people recommended this.</small></p></div>
  <div class="plugin"><i></i>Chatterbook social plugin</div>
</aside>

<aside class="widget tweets abs">
  <h3>Tweets</h3>
  <div class="follow"><i></i>Follow @ Hopalongdays</div>
  <div class="entry" style="top:38px"><div class="avatar" role="img" aria-label="Profile photo"></div><p><b>Dale Fenwick</b> <span class="handle">@dalefenwick</span><span class="age">18h</span><br>sit amet, coctetuer adipiscing elit, sed diam <span class="tag">@hopalongdays</span><br>sit amet, consectetu</p></div>
  <div class="entry" style="top:110px"><div class="avatar" role="img" aria-label="Profile photo"></div><p><b>Dale Fenwick</b> <span class="handle">@dalefenwick</span><span class="age">18h</span><br>sit amet, coctetuer adipiscing elit, sed diam <span class="tag">@hopalongdays</span><br>sit amet, consectetu</p></div>
  <div class="entry" style="top:182px"><div class="avatar" role="img" aria-label="Profile photo"></div><p><b>Dale Fenwick</b> <span class="handle">@dalefenwick</span><span class="age">18h</span><br>sit amet, coctetuer adipiscing elit, sed diam <span class="tag">@hopalongdays</span></p></div>
  <div class="tweet-box">Tweet to @hopalongdays</div>
</aside>

<aside class="widget videos abs">
  <div class="video-item" style="top:0"><div class="thumb" role="img" aria-label="Video still"><svg width="12" height="16"><path d="M0 0l12 8-12 8z" fill="#fff"/></svg><span>1:44</span></div><p>Lorem fdaafipsum dafsdolor sit amet, coctetuer adipiscing elit, sed diam<small>1 Day ago | 2345,views</small></p></div>
  <div class="video-item" style="top:69px"><div class="thumb" role="img" aria-label="Video still"><svg width="12" height="16"><path d="M0 0l12 8-12 8z" fill="#fff"/></svg><span>3:31</span></div><p>Lorem fdaafipsum dafsdolor sit amet, coctetuer adipiscing elit, sed diam<small>1 Day ago | 2345,views</small></p></div>
  <div class="video-item" style="top:138px"><div class="thumb" role="img" aria-label="Video still"><svg width="12" height="16"><path d="M0 0l12 8-12 8z" fill="#fff"/></svg><span>2:14</span></div><p>Lorem fdaafipsum dafsdolor sit amet, coctetuer adipiscing elit, sed diam<small>1 Day ago | 2345,views</small></p></div>
  <div class="video-item" style="top:207px;border-bottom:0"><div class="thumb" role="img" aria-label="Video still"><svg width="12" height="16"><path d="M0 0l12 8-12 8z" fill="#fff"/></svg><span>13'13"</span></div><p>Lorem fdaafipsum dafsdolor sit amet, coctetuer adipiscing elit, sed diam<small>1 Day ago | 2345,views</small></p></div>
</aside>

<footer class="site-footer abs">
  <div class="col quick-links">
    <h4>Quick Links</h4>
    <ul><li>Play Right Now</li><li>Get Invloved</li><li>Why Play</li><li>Fun Forever</li><li>Resources</li></ul>
  </div>
  <div class="col contact">
    <h4>Quick Contact</h4>
    <div style="top:37px"><svg width="9" height="12" viewBox="0 0 9 12"><path d="M4.5 0A4.5 4.5 0 0 0 0 4.5C0 8 4.5 12 4.5 12S9 8 9 4.5A4.5 4.5 0 0 0 4.5 0zm0 6.3a1.8 1.8 0 1 1 0-3.6 1.8 1.8 0 0 1 0 3.6z" fill="#333"/></svg><span>14 Larkfield Lane,<br>Leeds,<br>LS7 2QP</span></div>
    <div style="top:88px"><svg width="11" height="11" viewBox="0 0 11 11"><circle cx="5.5" cy="5.5" r="5" fill="none" stroke="#333"/><path d="M3.5 3c0 2.5 2 4.5 4.5 4.5" fill="none" stroke="#333" stroke-width="1.4"/></svg><span>0113-555-0142</span></div>
    <div style="top:112px"><svg width="11" height="9" viewBox="0 0 11 9"><rect x=".5" y=".5" width="10" height="8" fill="none" stroke="#333"/><path d="M.5.5l5 4 5-4" fill="none" stroke="#333"/></svg><span>info@hopalongdays.co.uk</span></div>
  </div>
  <div class="col social">
    <h4>Follow Us</h4>
    <div style="top:36px"><i></i>Chatterbook</div>
    <div style="top:64px"><i></i>Chirpline</div>
    <div style="top:93px"><i></i>ClipVault</div>
  </div>
  <div class="app">
    <div class="device" role="img" aria-label="Mobile phone showing the app"></div>
    <p>Get Hop Along Days on your</p>
    <p class="cta">MOBILE NOW</p>
  </div>
  <div class="guild">
    <strong>Northern Games &amp;<br>Crafts Guild</strong>
    <p>© 2010 Northern Games &amp; Crafts<br>Guild Ltd.<br>All Rights Reserved</p>
  </div>
</footer>

</body>
</html>
```